Stylish Business Cards Wanted

- DOUBLE SIDED Design Required -

High end, edgy cards for a corporate and personal stylist. Must include logo,
Name: Belinda Harwick
Title: Director and Stylist
telephone : +61 8 7142 5809
email: belinda@theloombriefing.example
website: theloombriefing.example
Tag: Corporate Workwear & Uniform Specialist | Personal Stylist
Would like nice icons for telephone, email, website

Target Market(s)

Businesses wanting stylish uniforms, people wanting stylish wardrobes

Industry/Entity Type

Corporate Workwear Stylist

Contact Information for Business Card

I would like black, white and gold foiling incorporated in the design - possibly a touch of the other colours on my branding guide attached Name: Belinda Harwick Title: Director and Stylist telephone : +61 8 7142 5809 email: belinda@theloombriefing.example website: theloombriefing.example Tag: Corporate Workwear & Uniform Specialist | Personal Stylist Would like nice icons for telephone, email, website

Font styles to use
Other font styles liked:
• Raleway

Colors

Designer to choose colors to be used in the design.

Requirements
Must have
• Gold foil accents

```html
<!DOCTYPE html>
<html lang="en">
<head>
<meta charset="utf-8">
<title>The Loom Briefing — Business Cards</title>
<link rel="stylesheet" href="https://fonts.googleapis.com/css2?family=Allura&family=Raleway:wght@400;500&display=swap">
<style>
  :root {
    --stage: #a3a3a3;
    --card-black: #221f20;
    --foil-gold: #e9b93f;
    --foil-white: #f1f1f1;
    --text-soft: #e6e6e6;
  }
  html, body {
    margin: 0;
    padding: 0;
    width: 1200px;
    height: 1050px;
    overflow: hidden;
    background: var(--stage);
  }
  .canvas {
    position: relative;
    width: 1200px;
    height: 1050px;
  }
  .card {
    position: absolute;
    left: 250px;
    width: 700px;
    height: 428px;
    background: var(--card-black);
    box-shadow: 0 0 0 3px var(--foil-gold), 0 18px 40px rgba(0,0,0,0.35);
    overflow: hidden;
    font-family: 'Raleway', sans-serif;
  }
  .card--front { top: 70px; }
  .card--back { top: 552px; }

  /* Front: content set on a portrait column turned to read upward */
  .contact-column {
    position: absolute;
    left: 136px;
    top: -136px;
    width: 428px;
    height: 700px;
    transform: rotate(-90deg);
    box-sizing: border-box;
    padding-top: 250px;
    text-align: center;
    color: var(--text-soft);
  }
  .holder-name {
    font-family: 'Allura', cursive;
    font-size: 64px;
    line-height: 1;
    color: var(--foil-white);
    margin: 0;
  }
  .holder-title {
    font-size: 14px;
    color: var(--foil-gold);
    margin: 4px 0 14px;
    letter-spacing: 0.3px;
  }
  .contact-icons {
    display: flex;
    justify-content: center;
    gap: 6px;
    margin-bottom: 18px;
  }
  .contact-icons svg { width: 26px; height: 26px; }
  .contact-lines, .service-lines {
    font-size: 14.5px;
    line-height: 1.45;
    margin: 0;
  }
  .divider {
    width: 24px;
    height: 1.5px;
    background: var(--foil-gold);
    margin: 22px auto;
  }

  /* Back: brand name */
  .brand {
    position: absolute;
    inset: 0;
    display: flex;
    align-items: center;
    justify-content: center;
    gap: 18px;
  }
  .brand-dot {
    width: 14px;
    height: 14px;
    border-radius: 50%;
    background: var(--foil-gold);
  }
  .brand-name {
    font-family: 'Raleway', sans-serif;
    font-weight: 500;
    font-size: 50px;
    letter-spacing: 2px;
    color: var(--foil-white);
    margin: 0;
  }
</style>
</head>
<body>
<main class="canvas">

  <section class="card card--front" aria-label="Business card front">
    <div class="contact-column">
      <h1 class="holder-name">Belinda Harwick</h1>
      <p class="holder-title">Director &amp; Stylist</p>

      <div class="contact-icons">
        <svg viewBox="0 0 26 26" role="img" aria-label="Telephone">
          <circle cx="13" cy="13" r="11.5" fill="none" stroke="var(--foil-gold)" stroke-width="2"/>
          <path d="M9.5 7.5l2 2.2-1.2 1.4c.7 1.6 2 2.9 3.6 3.6l1.4-1.2 2.2 2-1.3 1.7c-3.9-.4-7.8-4.3-8.2-8.2z" fill="var(--foil-gold)"/>
        </svg>
        <svg viewBox="0 0 26 26" role="img" aria-label="Email">
          <circle cx="13" cy="13" r="11.5" fill="none" stroke="var(--foil-gold)" stroke-width="2"/>
          <rect x="7" y="9" width="12" height="8.5" fill="var(--foil-gold)"/>
          <path d="M7 9l6 5 6-5" fill="none" stroke="var(--card-black)" stroke-width="1.2"/>
        </svg>
        <svg viewBox="0 0 26 26" role="img" aria-label="Website">
          <circle cx="13" cy="13" r="11.5" fill="none" stroke="var(--foil-gold)" stroke-width="2"/>
          <circle cx="13" cy="13" r="6" fill="var(--foil-gold)"/>
          <path d="M7 13h12M13 7c-2.5 3.5-2.5 8.5 0 12M13 7c2.5 3.5 2.5 8.5 0 12" fill="none" stroke="var(--card-black)" stroke-width="1"/>
        </svg>
      </div>

      <p class="contact-lines">
        +61 8 7142 5809<br>
        belinda@theloombriefing.example<br>
        theloombriefing.example
      </p>

      <div class="divider"></div>

      <p class="service-lines">
        Corporate Workwear<br>
        Uniform Specialist<br>
        Personal Stylist
      </p>
    </div>
  </section>

  <section class="card card--back" aria-label="Business card back">
    <div class="brand">
      <span class="brand-dot"></span>
      <p class="brand-name">The Loom Briefing</p>
    </div>
  </section>

</main>
</body>
</html>
```